GUARD AGAINST CLAIMS

I'm virtually ready to launch my site, but I have a number of edits and modifications that need to be implemented. More importantly, I'm always looking to improve my site, particularly now that I am making my proverbial "FIRST IMPRESSION." Thus, I'm willing to see if there is someone who can add creativity and perhaps improve what I already have, particularly on the All Important Front Page.

```html
<!DOCTYPE html>
<html lang="en">
<head>
<meta charset="utf-8">
<title>Guard Against Claims</title>
<link href="https://fonts.googleapis.com/css2?family=Tinos:wght@400;700&display=swap" rel="stylesheet">
<style>
:root{
  --red:#b0101c;
  --ink:#111;
  --grey:#555;
  --muted:#8a8a8a;
  --white:#fff;
  --black:#000;
  --line:#cfcfcf;
}
*{box-sizing:border-box;margin:0;padding:0}
html,body{width:1200px;height:3376px;overflow:hidden}
body{font-family:"Tinos","Times New Roman",serif;color:var(--ink);background:var(--white);position:relative}
.abs{position:absolute}

/* hero */
.hero{position:absolute;left:0;top:0;width:1200px;height:577px;background:linear-gradient(100deg,#140d09 0%,#2a1a12 35%,#5a3a25 60%,#3b2619 80%,#1c120c 100%)}
.hero-guide{position:absolute;top:0;width:1px;height:577px;background:rgba(255,255,255,.14)}
.brand{position:absolute;left:98px;top:20px;display:flex;align-items:center;gap:10px;color:var(--white);font-size:17px;font-weight:700}
.brand-dot{width:52px;height:52px;border-radius:50%;background:var(--red)}
.nav{position:absolute;top:46px;font-size:20px;color:var(--white)}
.phone-btn{position:absolute;left:900px;top:45px;width:200px;height:44px;background:var(--red);color:var(--white);font-size:19px;display:flex;align-items:center;padding-left:6px;gap:12px}
.phone-ico{width:36px;height:36px;border-radius:50%;background:var(--white);display:flex;align-items:center;justify-content:center}
.hero-kicker{left:100px;top:154px;font-size:33px;font-weight:700;color:var(--white)}
.hero-title{left:97px;top:206px;font-size:42px;font-weight:700;color:var(--white);white-space:nowrap}
.hero-text{left:98px;top:274px;width:480px;font-size:11.5px;line-height:25.7px;color:var(--white)}
.play{left:100px;top:438px;display:flex;align-items:center;gap:18px;color:var(--white);font-size:17px;font-weight:700}
.play-dot{width:40px;height:40px;border-radius:50%;background:var(--white);display:flex;align-items:center;justify-content:center}

/* about */
.about-title{left:98px;top:670px;font-size:38px;font-weight:700}
.about-sub{left:98px;top:726px;width:490px;font-size:24px;line-height:38px;color:#3a3a3a;font-weight:700}
.about-photo{left:97px;top:861px;width:498px;height:370px;background:linear-gradient(135deg,#6f7a86,#2c3b55 55%,#c8c3bb)}
.vertical-name{left:40px;top:1271px;transform:rotate(-90deg);transform-origin:left top;font-size:40px;font-weight:700;white-space:nowrap}
.about-text{left:673px;top:694px;width:432px;font-size:13.6px;line-height:25.7px;color:#222}
.about-text p+p{margin-top:25.7px}
.cta{left:673px;top:1183px;width:427px;height:47px;background:var(--red);color:var(--white);border-radius:0 24px 24px 0;font-size:17px;font-weight:700;display:flex;align-items:center;padding-left:24px}
.cta-dot{position:absolute;right:6px;top:6px;width:36px;height:36px;border-radius:50%;background:var(--white);display:flex;align-items:center;justify-content:center}

/* services */
.center{left:0;width:1200px;text-align:center}
.services-title{top:1352px;font-size:40px;font-weight:700}
.services-sub{left:180px;width:860px;top:1414px;font-size:16.5px;line-height:24px;color:var(--muted);font-weight:700;text-align:center}
.tile{position:absolute;width:400px;height:345px;display:flex;align-items:flex-end;justify-content:center;padding-bottom:30px;color:var(--white);font-size:21px;font-weight:700}
.t1{background:linear-gradient(160deg,#3d3b39,#1e1d1c)}
.t2{background:linear-gradient(160deg,#d8d8d6,#8d8c8a)}
.t3{background:linear-gradient(160deg,#6a6866,#3c3a38)}
.t4{background:linear-gradient(160deg,#4b4644,#2a2726)}
.t5{background:linear-gradient(160deg,#2f3633,#151b1a)}
.t6{background:linear-gradient(160deg,#6e7682,#3a4250)}
.tile-card{position:absolute;left:418px;top:1517px;width:364px;height:308px;background:var(--white);text-align:center;padding:20px 26px}
.tile-card h3{font-size:21px;line-height:30px}
.tile-card p{margin-top:20px;font-size:13.5px;line-height:22px;color:var(--grey)}
.tile-card a{display:inline-block;margin-top:28px;font-size:20px;font-weight:700;color:var(--ink);text-decoration:underline}

/* faq */
.faq-title{top:2284px;font-size:41px;font-weight:700}
.faq-sub{left:180px;width:840px;top:2358px;font-size:16px;line-height:24px;color:var(--muted);font-weight:700;text-align:center}
.faq-item{position:absolute;left:224px;width:752px;border:2px solid var(--line);border-radius:4px;font-size:14px;padding:0 20px;display:flex;align-items:center}
.faq-btn{position:absolute;right:4px;top:4px;width:54px;height:45px;background:var(--black);border-radius:6px;display:flex;align-items:center;justify-content:center}
.faq-open{display:block;padding-top:18px}
.faq-open p{margin-top:10px;width:620px;font-size:11.5px;line-height:21px;color:var(--muted)}

/* footer */
.footer{position:absolute;left:0;top:2971px;width:1200px;height:405px;background:var(--black);color:var(--white)}
.footer-badge{position:absolute;left:525px;top:2899px;width:150px;height:150px;border-radius:50%;background:var(--red);color:var(--white);font-size:16px;font-weight:700;display:flex;align-items:center;justify-content:center;text-align:center;line-height:20px}
.contact{position:absolute;top:3088px;display:flex;gap:14px}
.contact-ico{width:40px;height:40px;border-radius:50%;border:1px solid #888;display:flex;align-items:center;justify-content:center;flex:none}
.contact h4{font-size:14px}
.contact p{font-size:13px;line-height:18px;margin-top:4px}
.fnav{position:absolute;top:3193px;font-size:20px}
.frule{position:absolute;left:111px;top:3272px;width:976px;height:1px;background:#777}
.copy{top:3296px;font-size:16px}
</style>
</head>
<body>

<header class="hero">
  <div class="hero-photo abs" role="img" aria-label="Courtroom scene with judge and attorney" style="inset:0"></div>
  <div class="hero-guide" style="left:97px"></div>
  <div class="hero-guide" style="left:265px"></div>
  <div class="brand"><span class="brand-dot"></span>Guard Against Claims</div>
  <nav>
    <span class="nav" style="left:346px">Home</span>
    <span class="nav" style="left:452px">About</span>
    <span class="nav" style="left:558px">Services</span>
    <span class="nav" style="left:676px">Faq</span>
    <span class="nav" style="left:759px">Contact Us</span>
  </nav>
  <div class="phone-btn"><span class="phone-ico"><svg width="16" height="16" viewBox="0 0 24 24"><path d="M6.6 10.8a15 15 0 006.6 6.6l2.2-2.2a1 1 0 011-.25 11.4 11.4 0 003.6.57 1 1 0 011 1V20a1 1 0 01-1 1A17 17 0 013 4a1 1 0 011-1h3.5a1 1 0 011 1c0 1.25.2 2.45.57 3.57a1 1 0 01-.25 1z" fill="#b0101c"/></svg></span>+1 800.555.0142</div>
  <div class="abs hero-kicker">Welcome To</div>
  <h1 class="abs hero-title">GUARD AGAINST CLAIMS</h1>
  <p class="abs hero-text">Business Owners: Guard Against Claims (Gac) Is An Extremely Affordable Legal Service Plan (As Little As $8.00 Per Month) That Insulates Business Owners From Unwarranted Legal Claims And Expensive Lawsuits. Our Plan Uses Local, Experienced, Quality Attorneys Who Focus On Problem Prevention Using Proprietary Tools Available Only To Gac Members. Contact Us For A Free Consultation And Receive A Free Overview Of Your Business To See If You Are Truly Insulated From Legal Claims.</p>
  <div class="abs play"><span class="play-dot"><svg width="16" height="18" viewBox="0 0 16 18"><path d="M2 1l13 8-13 8z" fill="#b0101c"/></svg></span>Play Here</div>
</header>

<section class="about">
  <h2 class="abs about-title">ABOUT&nbsp; US</h2>
  <p class="abs about-sub">OUR UNIQUE SERVICE PLAN MAKES IT POSSIBLE FOR US TO GUARD AGAINST CLAIMS.</p>
  <div class="abs about-photo" role="img" aria-label="Smiling businessman in a navy suit at an office desk"></div>
  <div class="abs vertical-name">Edmund Hale.</div>
  <div class="abs about-text">
    <p>A homebuilding company was sued by a former employee who claimed to have been promised a more favorable sales area, which claim was disputed by the homebuilder. There was no evidence that such a promise had been made, other than the plaintiff's oral testimony. The company had the case dismissed, but spent $10,000 defending the case. And even though it was awarded its attorney's fees, the plaintiff proved uncollectible. Had the company been a GAC member, the case likely would never have been filed. Call for your FREE CONSULTATION and let us show you why the plaintiff likely would not have found a contingency attorney (as was the case) or been able to pay an attorney on an hourly basis. In short, by using GAC's services, the plaintiff's claim would not have been filed.</p>
    <p>In our vast experience with commercial litigation, we believe that a very large percentage of litigation cases hinge on "he said / she said" issues. By using GAC's services, we believe we can INSULATE you and your business from all such issues, which will MINIMIZE your EXPOSURE to LEGAL CLAIMS and LAWSUITS.</p>
  </div>
  <div class="abs cta">CONTACT US FOR A FREE CONSULTATION<span class="cta-dot"><svg width="20" height="20" viewBox="0 0 20 20"><circle cx="10" cy="10" r="9" fill="#111"/><path d="M5 10h8M10 6l4 4-4 4" stroke="#fff" stroke-width="2.2" fill="none"/></svg></span></div>
</section>

<section class="services">
  <h2 class="abs center services-title">OUR SERVICES</h2>
  <p class="abs services-sub">The price for a membership is a ridiculously low $9.95 PER WEEK. We believe that this fee is very affordable. So what is it? Membership includes the following:</p>
  <div class="tile t1" style="left:0;top:1504px" role="img" aria-label="Business meeting around a table">FREE INITIAL CONSULTATION</div>
  <div class="tile t2" style="left:400px;top:1504px" role="img" aria-label="Office team at work"></div>
  <div class="tile t3" style="left:800px;top:1504px" role="img" aria-label="Professional woman in an office">FREE CONSULTATION</div>
  <div class="tile t4" style="left:0;top:1849px" role="img" aria-label="Stressed man reading a letter">FREE ATTORNEY LETTERS</div>
  <div class="tile t5" style="left:400px;top:1849px" role="img" aria-label="Colleagues reviewing a laptop">LITIGATION DISCOUNTS</div>
  <div class="tile t6" style="left:800px;top:1849px" role="img" aria-label="Advisers reviewing documents with a client">COLLECTIONS</div>
  <div class="tile-card">
    <h3>PROPRIETARY CONTRACT LANGUAGE</h3>
    <p>GAC members are entitled to incorporate exclusive proprietary contract language in their contracts, work orders, and other written agreements in their business, that MINIMIZES EXPOSURE to legal claims against your business.</p>
    <a>Read More</a>
  </div>
</section>

<section class="faq">
  <h2 class="abs center faq-title">FREQUENTLY&nbsp; ASKED QUESTIONS</h2>
  <p class="abs faq-sub">Gac Is A Group Of Attorney And Legal Assistants With Many Years Of Experience In Litigation, Who Are Devoted To Preventing Legal Claims And Costly Lawsuits Through A Variety Of Free And Very Affordable Services Described Below.</p>
  <div class="faq-item" style="top:2438px;height:55px">Why should I be concerned about legal claims?<span class="faq-btn"><svg width="12" height="16"><path d="M1 1l10 7-10 7z" fill="#fff"/></svg></span></div>
  <div class="faq-item faq-open" style="top:2502px;height:125px">Provide more details about the value of GAC's contract language.
    <p>Lorem ipsum dolor sit amet, consectetur adipiscing elit. Suspendisse varius enim in eros elementum tristique. Duis cursus, mi quis viverra ornare, eros dolor interdum nulla, ut commodo diam libero vitae erat. Aenean faucibus nibh et justo cursus id rutrum lorem imperdiet. Nunc ut sem vitae risus tristique posuere.</p>
    <span class="faq-btn"><svg width="18" height="12"><path d="M1 1h16l-8 10z" fill="#fff"/></svg></span></div>
  <div class="faq-item" style="top:2637px;height:55px">If I'm a contractor, for example, how can a GAC membership minimize legal claims against my business?<span class="faq-btn"><svg width="12" height="16"><path d="M1 1l10 7-10 7z" fill="#fff"/></svg></span></div>
  <div class="faq-item" style="top:2705px;height:55px">What does a GAC membership cost?<span class="faq-btn"><svg width="12" height="16"><path d="M1 1l10 7-10 7z" fill="#fff"/></svg></span></div>
  <div class="faq-item" style="top:2772px;height:55px">Do you have a Referral Program?<span class="faq-btn"><svg width="12" height="16"><path d="M1 1l10 7-10 7z" fill="#fff"/></svg></span></div>
</section>

<footer class="footer"></footer>
<div class="footer-badge">Guard<br>Against<br>Claims</div>
<div class="contact" style="left:173px;color:#fff">
  <span class="contact-ico"><svg width="16" height="12" viewBox="0 0 16 12"><rect x="1" y="1" width="14" height="10" fill="none" stroke="#fff"/><path d="M1 1l7 6 7-6" fill="none" stroke="#fff"/></svg></span>
  <div><h4>EMAIL</h4><p>hello@guardagainstclaims.com</p></div>
</div>
<div class="contact" style="left:504px;top:3092px;color:#fff">
  <span class="contact-ico"><svg width="12" height="16" viewBox="0 0 12 16"><path d="M6 15s5-5.5 5-9A5 5 0 001 6c0 3.5 5 9 5 9z" fill="none" stroke="#fff"/><circle cx="6" cy="6" r="1.8" fill="#fff"/></svg></span>
  <div><h4>OUR LOCATION</h4><p>4820 West Harbor Ave., Suite 210, Cedar Falls,<br>Oregon 97401</p></div>
</div>
<div class="contact" style="left:863px;color:#fff">
  <span class="contact-ico"><svg width="14" height="14" viewBox="0 0 24 24"><path d="M6.6 10.8a15 15 0 006.6 6.6l2.2-2.2a1 1 0 011-.25 11.4 11.4 0 003.6.57 1 1 0 011 1V20a1 1 0 01-1 1A17 17 0 013 4a1 1 0 011-1h3.5a1 1 0 011 1c0 1.25.2 2.45.57 3.57a1 1 0 01-.25 1z" fill="#fff"/></svg></span>
  <div><h4>PHONE NUMBER</h4><p>+1 800-555-0187</p></div>
</div>
<nav style="color:#fff">
  <span class="fnav" style="left:346px">Home</span>
  <span class="fnav" style="left:452px">About</span>
  <span class="fnav" style="left:558px">Services</span>
  <span class="fnav" style="left:676px">Faq</span>
  <span class="fnav" style="left:759px">Contact Us</span>
</nav>
<div class="frule"></div>
<div class="abs center copy" style="color:#fff">© Copyrights 2023&nbsp; Guard Against Claims |&nbsp; All Rights Reserved</div>

</body>
</html>
```